Modern design company business card design

We are a design oriented construction firm. The owner is an architect and licensed General Contractor and accomplished furniture designer. We do new home construction and large scale remodeling and office design. We would like a design for our new business cards that is clean and modern, but relatable. We like the bright green color of our logo mixed with different shades of grey. We're also open to reinterpreting the logo.

Target Market(s)

Potential design clients,
Construction clients

Industry/Entity Type

Architecture

Contact Information for Business Card

Tall Maple Design | Build Inc. (optional with logo, Inc. optional)Jeffrey MorganOwner (optional)317.555.0148 cell317.431.8056 officejmorgan@greensquareinc.comwww.greensquareinc.com

Font styles to use
Sans Serif
Other font styles liked:
• Avenir

Requirements
Nice to have
• I like designs that have some continuity between the front and back, i.e. similar layouts or graphic elements that wrap around the card. I tend to prefer horizontal over vertical, but that's not a have to. I also tend to prefer white or recycled paper.

```html
<!DOCTYPE html>
<html lang="en">
<head>
<meta charset="utf-8">
<title>Tall Maple Design | Build – Business Cards</title>
<link rel="stylesheet" href="https://fonts.googleapis.com/css2?family=Open+Sans:wght@400;600;700&display=swap">
<style>
  :root {
    --backdrop: #e6e6e4;
    --card-dark-1: #55585d;
    --card-dark-2: #3b3d41;
    --card-light: #f7f7f7;
    --brand-green: #7cc242;
    --band-green: #3aaa48;
    --text-light: #e4e5e6;
    --text-soft: #c9cbcd;
    --text-grey: #9a9c9e;
    --rule: #d9dadb;
    --paper-white: #ffffff;
  }
  * { box-sizing: border-box; margin: 0; padding: 0; }
  html, body {
    width: 1200px; height: 913px; overflow: hidden;
    background: var(--backdrop);
    font-family: "Open Sans", sans-serif;
  }
  .stage { position: relative; width: 1200px; height: 913px; }

  .card {
    position: absolute; width: 560px; height: 320px;
    overflow: hidden;
    box-shadow: 0 10px 28px rgba(0,0,0,.18);
  }

  /* Company name */
  .company { position: absolute; display: flex; align-items: center; gap: 12px; }
  .company__dot { border-radius: 50%; background: var(--brand-green); flex: none; }
  .company__name { font-weight: 400; white-space: nowrap; }

  /* Front */
  .card--front {
    left: 40px; top: 120px;
    background: linear-gradient(160deg, var(--card-dark-1), var(--card-dark-2));
    color: var(--text-light);
  }
  .card--front .company { left: 28px; top: 104px; }
  .card--front .company__dot { width: 14px; height: 14px; }
  .card--front .company__name { font-size: 20px; color: var(--text-light); }

  .holder {
    position: absolute; right: 40px; top: 44px;
    font-weight: 700; font-size: 15px; letter-spacing: .04em; text-transform: uppercase;
    color: var(--paper-white);
  }
  .rule { position: absolute; height: 1px; background: var(--rule); }
  .rule--top { left: 160px; right: 40px; top: 72px; }
  .rule--contact { left: 28px; width: 300px; top: 186px; }

  .contacts {
    position: absolute; left: 28px; top: 196px; list-style: none;
    font-size: 13px; line-height: 19px; color: var(--text-soft);
  }
  .contacts li { display: flex; align-items: center; gap: 8px; }
  .contacts svg { width: 11px; height: 11px; fill: var(--band-green); flex: none; }

  .band { position: absolute; bottom: 0; }
  .band--white { left: 0; width: 355px; height: 30px; background: var(--paper-white); }
  .band--green { right: 0; width: 205px; height: 56px; background: var(--band-green); }

  /* Back */
  .card--back {
    left: 600px; top: 470px;
    background: var(--card-light);
  }
  .card--back .company { left: 0; right: 0; top: 140px; justify-content: center; }
  .card--back .company__dot { width: 20px; height: 20px; }
  .card--back .company__name { font-size: 30px; color: var(--text-grey); }
</style>
</head>
<body>
<main class="stage">

  <section class="card card--front" aria-label="Business card front">
    <div class="company">
      <span class="company__dot"></span>
      <p class="company__name">Tall Maple Design | Build</p>
    </div>

    <p class="holder">Dennis Holloway</p>
    <div class="rule rule--top"></div>
    <div class="rule rule--contact"></div>

    <ul class="contacts">
      <li><svg viewBox="0 0 12 12"><path d="M2 1h3l1 3-2 1a7 7 0 0 0 3 3l1-2 3 1v3c-6 0-9-3-9-9z"/></svg>317.555.0172</li>
      <li><svg viewBox="0 0 12 12"><rect x="3" y="0" width="6" height="12" rx="1"/></svg>317.555.0148</li>
      <li><svg viewBox="0 0 12 12"><circle cx="6" cy="6" r="5"/></svg>www.tallmapleinc.example</li>
      <li><svg viewBox="0 0 12 12"><path d="M0 2h12v8H0z"/></svg>dholloway@tallmapleinc.example</li>
    </ul>

    <div class="band band--white"></div>
    <div class="band band--green"></div>
  </section>

  <section class="card card--back" aria-label="Business card back">
    <div class="company">
      <span class="company__dot"></span>
      <p class="company__name">Tall Maple Design | Build</p>
    </div>
  </section>

</main>
</body>
</html>
```